Brewlark Cup Society - A Monthly Subscription Coffee Club - Shopify Website Design

A monthly subscription company. Need a Shopify Website Design and uploaded to fully work with Tidal Renewals.

Please look at these sites for examples as well as the images I enclosed.

https://www.sipvantor.com/
https://mokrate.com/
https://www.platewinder.com/
https://www.globunchies.com/

Number of Pages Required

1 page

```html
<!DOCTYPE html>
<html lang="en">
<head>
<meta charset="utf-8">
<title>Brewlark Cup Society — Coffee Club</title>
<link href="https://fonts.googleapis.com/css2?family=Lora:ital,wght@0,400;0,600;0,700;1,400&family=Montserrat:wght@400;500;600&family=Josefin+Sans:wght@400;600&display=swap" rel="stylesheet">
<style>
  :root{
    --bg:#ebe7e2;
    --ink:#2b2420;
    --muted:#6f6660;
    --bar:#3b2a22;
    --accent:#5b3a26;
    --line:#cfc8c0;
    --white:#ffffff;
  }
  *{box-sizing:border-box;margin:0;padding:0}
  html,body{width:1200px;height:3200px;overflow:hidden}
  body{background:var(--bg);color:var(--ink);font-family:"Montserrat",sans-serif;position:relative}
  .abs{position:absolute}
  .announce{top:0;left:0;width:1200px;height:34px;background:var(--bar);color:#f3ece6;font-size:12px;display:flex;align-items:center;justify-content:center;letter-spacing:.3px}
  .header{top:34px;left:0;width:1200px;height:150px}
  .search{left:108px;top:44px;font-size:13px;color:var(--muted)}
  .logo{left:0;width:1200px;top:34px;text-align:center;font-family:"Josefin Sans",sans-serif;font-size:30px;letter-spacing:5px;text-transform:uppercase;font-weight:400}
  .icons{right:108px;top:42px;display:flex;gap:16px}
  .nav{top:118px;left:0;width:1200px;display:flex;justify-content:center;gap:40px;font-size:12px;font-weight:600;letter-spacing:1px}
  .hero{top:212px;left:108px;width:984px;height:500px;background:linear-gradient(120deg,#2c2520 0%,#6b5446 45%,#3a302a 75%,#857366 100%)}
  .hero-text{top:212px;left:108px;width:984px;height:500px;display:flex;flex-direction:column;align-items:center;justify-content:center;color:var(--white);text-align:center}
  .hero-kicker{font-family:"Lora",serif;font-style:italic;font-size:17px;opacity:.9}
  .hero-title{font-family:"Lora",serif;font-size:64px;font-weight:400;margin:6px 0 28px}
  .btn{display:inline-block;background:var(--accent);color:var(--white);font-size:13px;font-weight:600;padding:15px 30px}
  .rule{left:108px;width:984px;height:1px;background:var(--line)}
  .notice{top:784px;left:200px;width:800px;text-align:center;font-family:"Lora",serif;font-size:21px;line-height:1.5}
  .product{width:240px;text-align:center}
  .product-shot{width:240px;height:260px;background:linear-gradient(160deg,#fafafa 0%,#dedad6 60%,#c9c2bb 100%)}
  .product-name{font-family:"Lora",serif;font-size:22px;margin-top:72px}
  .product-price{font-size:11px;color:var(--muted);margin-top:8px}
  .post{width:480px}
  .post-date{font-size:11px;letter-spacing:1px;color:var(--muted);text-align:center}
  .post-title{font-family:"Lora",serif;font-size:22px;font-weight:600;text-align:center;margin-top:12px;white-space:nowrap}
  .post-shot{height:312px;margin-top:20px}
  .post-copy{font-size:15px;line-height:1.55;color:#4a423d;margin-top:22px}
  .post-link{display:inline-block;margin-top:56px;font-size:15px;border-bottom:1px solid var(--ink);padding-bottom:2px}
  .join{top:2650px;left:0;width:1200px;text-align:center}
  .join h2{font-family:"Lora",serif;font-size:38px;font-weight:600}
  .join p{font-size:14px;color:var(--muted);margin-top:18px}
  .signup{display:flex;justify-content:center;gap:28px;margin-top:34px}
  .email{width:252px;height:60px;background:var(--white);font-size:14px;display:flex;align-items:center;padding-left:24px;text-align:left}
  .subscribe{width:180px;height:60px;background:var(--accent);color:var(--white);font-size:14px;font-weight:600;display:flex;align-items:center;justify-content:center}
  .foot-col{top:2934px}
  .foot-col h3{font-family:"Lora",serif;font-size:20px;font-weight:600;margin-bottom:22px}
  .foot-col li{list-style:none;font-size:13px;line-height:1.9}
  .foot-col p{font-size:13px;line-height:1.6;margin-bottom:22px}
  .social{display:flex;gap:12px}
  .social span{width:16px;height:16px;border-radius:50%;background:var(--ink)}
  .legal{top:3156px;left:108px;font-size:13px}
  .pay{top:3154px;right:108px;display:flex;gap:6px}
  .pay span{width:26px;height:16px;background:#b9b1a9}
</style>
</head>
<body>
  <div class="abs announce">We are now offering local delivery on Sundays. Place your order before Saturday 3:00pm!</div>

  <header class="abs header">
    <div class="abs search">Search</div>
    <div class="abs logo">Brewlark Cup Society</div>
    <div class="abs icons">
      <svg width="22" height="22" viewBox="0 0 22 22" fill="none" stroke="#2b2420" stroke-width="1.6"><circle cx="11" cy="11" r="9"/><circle cx="11" cy="9" r="3.2"/><path d="M5 17.5c1.6-2.6 3.6-3.6 6-3.6s4.4 1 6 3.6"/></svg>
      <svg width="20" height="22" viewBox="0 0 20 22" fill="none" stroke="#2b2420" stroke-width="1.6"><path d="M3 7h14l-1 13H4z"/><path d="M7 9V5a3 3 0 0 1 6 0v4"/></svg>
    </div>
    <nav class="abs nav"><span>SHOP</span><span>SUBSCRIPTION</span><span>ABOUT US ⌄</span><span>CONTACT</span></nav>
  </header>

  <div class="abs hero" role="img" aria-label="Barista carrying a sack of coffee beans inside a roastery"></div>
  <div class="abs hero-text">
    <div class="hero-kicker">We are a Monthly Subscription</div>
    <div class="hero-title">Coffee Club</div>
    <span class="btn">Browse Beans</span>
  </div>

  <div class="abs rule" style="top:752px"></div>
  <p class="abs notice"><strong>Due to COVID</strong>, we are only operating as a takeout window. Our online shop is always open and the beans we offer continue to rotate, depending on what is available to our roastery!</p>
  <div class="abs rule" style="top:900px"></div>

  <div class="abs product" style="left:160px;top:1020px"><div class="product-shot" role="img" aria-label="Coffee gift box with beans"></div><div class="product-name">Espresso</div><div class="product-price">from $25.00</div></div>
  <div class="abs product" style="left:480px;top:1020px"><div class="product-shot" role="img" aria-label="Open box of assorted coffee packs"></div><div class="product-name">Espresso</div><div class="product-price">from $25.00</div></div>
  <div class="abs product" style="left:800px;top:1020px"><div class="product-shot" role="img" aria-label="Coffee pod box with packaging"></div><div class="product-name">Espresso</div><div class="product-price">from $25.00</div></div>

  <div class="abs product" style="left:160px;top:1496px"><div class="product-shot" role="img" aria-label="Bag of roasted coffee"></div><div class="product-name">Espresso</div><div class="product-price">from $25.00</div></div>
  <div class="abs product" style="left:480px;top:1496px"><div class="product-shot" role="img" aria-label="Three coffee bags in a set"></div><div class="product-name">Espresso</div><div class="product-price">from $25.00</div></div>
  <div class="abs product" style="left:800px;top:1496px"><div class="product-shot" role="img" aria-label="Two kraft paper coffee bags"></div><div class="product-name">Espresso</div><div class="product-price">from $25.00</div></div>

  <div class="abs rule" style="top:1950px"></div>

  <article class="abs post" style="left:108px;top:2004px">
    <div class="post-date">AUGUST 1ST, 2020</div>
    <div class="post-title">4 ways to elevate your morning routine</div>
    <div class="post-shot" role="img" aria-label="Friends toasting coffee cups around a table" style="background:linear-gradient(135deg,#3b2d25,#8a6e58 50%,#c9b8a5)"></div>
    <p class="post-copy">Lorem ipsum dolor sit amet, consectetur adipiscing elit, sed do eiusmod tempor incididunt ut labore et dolore magna aliqua. Ut enim ad minim veniam, quis nostrud exercitation ullamco laboris nisi.</p>
    <span class="post-link">Continue Reading</span>
  </article>
  <article class="abs post" style="left:612px;top:2004px">
    <div class="post-date">AUGUST 1ST, 2020</div>
    <div class="post-title">Which is for you? French Press vs. Pour Over</div>
    <div class="post-shot" role="img" aria-label="Barista preparing coffee at a bar counter" style="background:linear-gradient(135deg,#2a2623,#6d625a 50%,#b8aea4)"></div>
    <p class="post-copy">Lorem ipsum dolor sit amet, consectetur adipiscing elit, sed do eiusmod tempor incididunt ut labore et dolore magna aliqua. Ut enim ad minim veniam, quis nostrud exercitation ullamco laboris nisi.</p>
    <span class="post-link">Continue Reading</span>
  </article>

  <div class="abs rule" style="top:2620px"></div>

  <section class="abs join">
    <h2>Join The Family</h2>
    <p>Sign up to our newsletter to receive updates about our future roasts!</p>
    <div class="signup"><div class="email">Email Address</div><div class="subscribe">Subscribe</div></div>
  </section>

  <div class="abs rule" style="top:2908px"></div>

  <div class="abs foot-col" style="left:108px"><h3>Social</h3><div class="social" aria-label="Social links"><span></span><span></span><span></span><span></span></div></div>
  <div class="abs foot-col" style="left:432px"><h3>Navigate</h3><ul><li>Shop</li><li>Subscription</li><li>About Us</li><li>Contact</li></ul></div>
  <div class="abs foot-col" style="left:776px;width:316px"><h3>Local Curbside Pickup</h3><p>We are working to fulfill all base orders and are offering safe pickup from Monday-Saturday!</p><p>Please contact us with any questions.</p></div>

  <div class="abs rule" style="top:3124px"></div>
  <div class="abs legal">© 2020 &nbsp;|&nbsp; www.brewlarkcup.com</div>
  <div class="abs pay" aria-label="Accepted payments"><span></span><span></span></div>
</body>
</html>
```